Real Estate Company Looking for Business Card Designs for 3 Executives

Hello!
Thanks so much for considering our project! We are a real estate investment company located in Edmonton, Alberta called Bellhaven Group of Companies. We invest/develop both commercial and residential real estate and are looking to create 3 DOUBLE-SIDED business cards for 3 top executives in the company! (for some reason it won't let us select the double-sided option, but yes, the cards are double sided and would be happy to tip extra)

We have certain guidelines that we want our business cards to for sure follow - the back of the Business card has to be the Black Background Version of the Logo which has already been designed and linked as a file (first file). We want the entire back of the card to simply just be the black background logo. In terms of the front of the card, would like to see a smaller version of the white background logo (linked as the second file) in the top left hand corner - of course, feel free to get creative and we can make revisions together along the way! and Then after that, just text. We want the card to be sharp, clean, easy on the eyes and highly professional looking. We would like the card to include the Full name of the Company (Bellhaven Group of Companies), Name of the Person, Title, Phone, Email. If possible please provide the front part of the card for 3 people:

1) Bellhaven Group of Companies, Liora Quenby, Chief Financial Officer, 780-555-0142, lioraquenby@bellhavengroup.example

2) Bellhaven Group of Companies, Tobias Quenby, Chief Executive Officer, 780-555-0187, tobiasquenby@bellhavengroup.example

3) Bellhaven Group of Companies, Rui Delcourt, Chief Operations Officer, 587-555-0163, ruidelcourt@bellhavengroup.example

Thank you so much for considering our project & we look forward to seeing your designs!

```html
<!DOCTYPE html>
<html lang="en">
<head>
<meta charset="utf-8">
<title>Bellhaven Group of Companies – Business Card</title>
<link rel="stylesheet" href="https://fonts.googleapis.com/css2?family=Arimo:wght@400&family=Tinos:wght@700&display=swap">
<style>
  :root {
    --backdrop: #262626;
    --card-front: #ffffff;
    --card-back: #1f1f1f;
    --ink: #1c1c1c;
    --back-mark: #3a3a3a;
  }
  * { box-sizing: border-box; margin: 0; padding: 0; }
  html, body {
    width: 1200px; height: 1059px; overflow: hidden;
    background: var(--backdrop);
  }
  .canvas { position: relative; width: 1200px; height: 1059px; }

  .card { position: absolute; width: 690px; height: 392px; }
  .card--front { left: 256px; top: 89px; background: var(--card-front); }
  .card--back  { left: 254px; top: 547px; background: var(--card-back); }

  .brand {
    position: absolute; left: 66px; top: 128px; width: 210px;
    font-family: "Arimo", sans-serif; font-weight: 400; color: var(--ink);
    display: flex; align-items: center; gap: 10px;
  }
  .brand__square { width: 14px; height: 14px; background: var(--ink); flex: none; }
  .brand__name { font-size: 17px; line-height: 1.25; letter-spacing: 1.5px; text-transform: uppercase; }

  .details { position: absolute; left: 340px; top: 124px; color: var(--ink); }
  .details__name {
    font-family: "Tinos", serif; font-weight: 700; font-size: 22px; letter-spacing: 0.3px;
  }
  .details__title {
    font-family: "Arimo", sans-serif; font-size: 16px; margin-top: 4px;
  }
  .details__rule { width: 296px; height: 1px; background: var(--ink); margin: 14px 0 13px; }
  .contact { list-style: none; font-family: "Arimo", sans-serif; font-size: 16px; }
  .contact li { display: flex; align-items: center; gap: 7px; height: 25.5px; }
  .contact svg { width: 12px; height: 12px; fill: var(--ink); flex: none; }

  .back-brand {
    position: absolute; inset: 0; display: flex; align-items: center; justify-content: center;
    font-family: "Arimo", sans-serif; font-weight: 400; font-size: 34px; letter-spacing: 6px;
    text-transform: uppercase; color: var(--back-mark);
  }
</style>
</head>
<body>
<main class="canvas">
  <section class="card card--front">
    <div class="brand">
      <span class="brand__square"></span>
      <span class="brand__name">Bellhaven Group of Companies</span>
    </div>
    <div class="details">
      <h1 class="details__name">TOBIAS QUENBY</h1>
      <p class="details__title">Chief Executive Officer</p>
      <div class="details__rule"></div>
      <ul class="contact">
        <li>
          <svg viewBox="0 0 24 24" aria-hidden="true"><path d="M6.6 10.8a15.1 15.1 0 0 0 6.6 6.6l2.2-2.2c.3-.3.7-.4 1-.2 1.1.4 2.3.6 3.6.6.6 0 1 .4 1 1V20c0 .6-.4 1-1 1A17 17 0 0 1 3 4c0-.6.4-1 1-1h3.5c.6 0 1 .4 1 1 0 1.3.2 2.5.6 3.6.1.3 0 .7-.2 1z"/></svg>
          780-555-0187
        </li>
        <li>
          <svg viewBox="0 0 24 24" aria-hidden="true"><path d="M2 5h20v14H2zm2 2v.5l8 5 8-5V7l-8 5z"/></svg>
          tobiasquenby@bellhavengroup.example
        </li>
        <li>
          <svg viewBox="0 0 24 24" aria-hidden="true"><circle cx="12" cy="12" r="10"/></svg>
          www.bellhavengroup.example
        </li>
      </ul>
    </div>
  </section>

  <section class="card card--back">
    <div class="back-brand">Bellhaven</div>
  </section>
</main>
</body>
</html>
```